Salon and Spa Distributor Business Card

Need a business card. We are are distributor in the salon and spa industry. We identify with natural beauty. Need a card with:
Company Name: Petal Quarry"
Title: "President & CEO"
Address
Company Phone number
email
website
Tag Line:" The Professional Salon Source"

Industry/Entity Type

Business

Contact Information for Business Card

Name: Dov Strommen
Title: "President & CEO"
Address: 31 Harlow Ln, Bexmoor, NJ 07813
Company Phone number: 800-463-5918
email: dovstrommen@petalquarry.example
website: www.petalquarry.example

Requirements
Should not have
• No black backgrounds

```html
<!DOCTYPE html>
<html lang="en">
<head>
<meta charset="utf-8">
<title>Petal Quarry – Business Card</title>
<link href="https://fonts.googleapis.com/css2?family=Source+Sans+3:ital,wght@0,400;0,600;1,400&display=swap" rel="stylesheet">
<style>
  :root {
    --backdrop: #ebe8e4;
    --card-white: #ffffff;
    --brand-green: #1f8a3e;
    --brand-green-dark: #0e6e34;
    --brand-green-light: #5bbb47;
    --text-dark: #3d3d3d;
    --text-grey: #8a8a8a;
    --rule-grey: #cfcfcf;
  }
  * { box-sizing: border-box; margin: 0; padding: 0; }
  html, body {
    width: 1200px; height: 987px; overflow: hidden;
    background: var(--backdrop);
    font-family: "Source Sans 3", "Myriad Pro", sans-serif;
  }
  .canvas { position: relative; width: 1200px; height: 987px; }

  .card {
    position: absolute; left: 293px; width: 615px; height: 351px;
    box-shadow: 0 3px 10px rgba(0,0,0,0.25);
  }

  /* Front */
  .card--front { top: 130px; background: var(--card-white); overflow: hidden; }
  .front__brand {
    position: absolute; left: 36px; top: 157px;
    display: flex; align-items: center; gap: 10px;
    font-size: 23px; font-weight: 400; color: var(--brand-green-light);
  }
  .front__brand-dot {
    width: 16px; height: 16px; border-radius: 50%;
    background: var(--brand-green-light);
  }
  .front__divider {
    position: absolute; left: 305px; top: 87px; width: 1px; height: 187px;
    background: var(--rule-grey);
  }
  .front__details { position: absolute; left: 326px; top: 83px; color: var(--text-dark); }
  .details__name { font-size: 23px; font-weight: 600; color: var(--brand-green); line-height: 1.15; }
  .details__title { font-size: 16.5px; color: var(--text-grey); line-height: 1.25; margin-bottom: 10px; }
  .details__address { font-size: 16.5px; line-height: 22px; margin-bottom: 6px; }
  .details__contact { list-style: none; font-size: 16px; line-height: 23.5px; }
  .details__contact li { display: flex; align-items: center; gap: 9px; white-space: nowrap; }
  .details__contact svg { width: 14px; height: 14px; fill: var(--brand-green); flex: none; }
  .front__band-rule {
    position: absolute; left: 0; right: 0; top: 328px; height: 3px;
    background: linear-gradient(#bdbdbd, #e6e6e6);
  }
  .front__band {
    position: absolute; left: 0; right: 0; bottom: 0; height: 20px;
    background: linear-gradient(90deg, var(--brand-green-dark), var(--brand-green-light) 50%, var(--brand-green-dark));
  }

  /* Back */
  .card--back {
    top: 506px;
    background: radial-gradient(ellipse 60% 70% at 50% 45%, #5fbf4a 0%, #2f9a40 45%, var(--brand-green-dark) 100%);
    color: #fff; text-align: center;
  }
  .back__brand {
    position: absolute; left: 0; right: 0; top: 148px;
    display: flex; justify-content: center; align-items: center; gap: 14px;
    font-size: 40px; font-weight: 400;
  }
  .back__brand-dot { width: 22px; height: 22px; border-radius: 50%; background: #fff; }
  .back__tagline {
    position: absolute; left: 0; right: 0; top: 290px;
    font-size: 16.5px; font-style: italic;
  }
</style>
</head>
<body>
<div class="canvas">
  <section class="card card--front" aria-label="Business card front">
    <div class="front__brand"><span class="front__brand-dot"></span>Petal Quarry</div>
    <div class="front__divider"></div>
    <div class="front__details">
      <p class="details__name">Dov Strommen</p>
      <p class="details__title">President &amp; CEO</p>
      <p class="details__address">31 Harlow Ln<br>Bexmoor, NJ 07813</p>
      <ul class="details__contact">
        <li><svg viewBox="0 0 16 16" aria-hidden="true"><path d="M3.5 1 6 3.8 4.7 5.6c.9 2.2 3.4 4.8 5.7 5.7l1.8-1.3L15 12.5 13.2 15C6.7 14.6 1.4 9.3 1 2.8Z"/></svg>800-463-5918</li>
        <li><svg viewBox="0 0 16 16" aria-hidden="true"><path d="M1 3h14v1.2L8 8.7 1 4.2Z"/><path d="M1 5.6l7 4.5 7-4.5V13H1Z"/></svg>dovstrommen@petalquarry.example</li>
        <li><svg viewBox="0 0 16 16" aria-hidden="true"><circle cx="8" cy="8" r="7"/><path d="M5 4.5c1.5.2 2 1.4 1.2 2.3-.8.8.3 2 1.4 1.7 1.2-.3 1.7 1 1 2.2-.5.9-.2 2 .5 2.6" fill="none" stroke="#fff" stroke-width="1.3"/></svg>www.petalquarry.example</li>
      </ul>
    </div>
    <div class="front__band-rule"></div>
    <div class="front__band"></div>
  </section>

  <section class="card card--back" aria-label="Business card back">
    <div class="back__brand"><span class="back__brand-dot"></span>Petal Quarry</div>
    <p class="back__tagline">The Professional Salon Source</p>
  </section>
</div>
</body>
</html>
```